Inspirational Quotes Poster Set

Brookloft is a stylish coworking space, which has a design-oriented vintage look from the 60's with an industrial touch (www.brookloft-example.com) Brookloft Quote Poster Set of 16 posters. The poster should be typo oriented and rather simple. Reflecting a bit the clean billboard design from the sixties. Minimal / simple graphical elements

Target Market(s)

Startups and Entrepreneurs

Industry/Entity Type

Startup

Font styles to use
Sans Serif

Colors

Designer to choose colors to be used in the design.

Requirements
Must have
• Posters need to be on and very stylish

```html
<!DOCTYPE html>
<html lang="en">
<head>
<meta charset="utf-8">
<title>Brookloft Quote Poster Set – Risk Taker</title>
<link href="https://fonts.googleapis.com/css2?family=Bebas+Neue&family=Carlito&display=swap" rel="stylesheet">
<style>
  :root {
    --poster-bg: #d0807c;
    --ink: #ffffff;
  }
  html, body {
    margin: 0;
    padding: 0;
    overflow: hidden;
    background: var(--poster-bg);
  }
  .poster {
    position: relative;
    width: 738px;
    height: 1200px;
    background: var(--poster-bg);
    overflow: hidden;
  }
  .poster__art {
    position: absolute;
    left: 303px;
    top: 0;
    width: 156px;
    height: 291px;
    background: var(--ink);
    border-radius: 0 0 78px 78px;
  }
  .poster__type {
    position: absolute;
    inset: 0;
  }
  .quote {
    font-family: "Bebas Neue", "Oswald", sans-serif;
    fill: var(--ink);
  }
  .quote--lead { font-size: 108px; }
  .quote--hero { font-size: 151px; }
  .quote--tail { font-size: 86px; }
  .credit {
    font-family: "Carlito", "Calibri", sans-serif;
    font-size: 33px;
    fill: var(--ink);
  }
</style>
</head>
<body>
  <main class="poster">
    <div class="poster__art" role="img" aria-label="Simple white hanging rope loop icon"></div>
    <svg class="poster__type" width="738" height="1200" viewBox="0 0 738 1200">
      <text class="quote quote--lead" x="90" y="460" textLength="536" lengthAdjust="spacingAndGlyphs" transform="skewX(-10) translate(81 0)">IF YOU’RE NOT A</text>
      <text class="quote quote--hero" x="92" y="605" textLength="532" lengthAdjust="spacingAndGlyphs">RISK TAKER</text>
      <text class="quote quote--tail" x="149" y="707" textLength="415" lengthAdjust="spacingAndGlyphs">YOU SHOULD GET</text>
      <text class="quote quote--tail" x="147" y="807" textLength="419" lengthAdjust="spacingAndGlyphs">THE HELL OUT OF</text>
      <text class="quote quote--tail" x="238" y="908" textLength="239" lengthAdjust="spacingAndGlyphs">BUSINESS</text>
      <text class="credit" x="369" y="1060" text-anchor="middle">Dale Fenwick</text>
      <text class="credit" x="369" y="1114" text-anchor="middle">Burgerline Founder</text>
    </svg>
  </main>
</body>
</html>
```